New Business Card Design Project

Use the flyer uploaded and website www.brightoakbuilders.com for inspiration.
List Our Services on Backside of business cards
Marcus Delling
Harborline Builders Inc.
Licensed General Contractors
858-471-6093

Contact Information for Business Card

Use the flyer uploaded and website www.brightoakbuilders.com for inspiration. List Our Services on Backside of business cards Marcus Delling Harborline Builders Inc. Licensed General Contractors 858-471-6093

```html
<!DOCTYPE html>
<html lang="en">
<head>
<meta charset="utf-8">
<title>Harborline Builders – Business Cards</title>
<link rel="stylesheet" href="https://fonts.googleapis.com/css2?family=Roboto:wght@400;500;700;900&display=swap">
<style>
  :root{
    --stage:#1e1e1f;
    --card-dark:#232226;
    --card-light:#ffffff;
    --red:#e31b23;
    --blue:#4a74c9;
    --ink:#1b1b1b;
    --white:#ffffff;
    --photo-a:#dfe6ec;
    --photo-b:#a9c6e0;
  }
  *{box-sizing:border-box;margin:0;padding:0}
  html,body{width:1200px;height:780px;overflow:hidden;background:var(--stage);font-family:"Roboto",sans-serif}
  .stage{position:relative;width:1200px;height:780px}
  .card{position:absolute;top:235px;width:540px;height:310px;overflow:hidden;border-radius:2px}
  .card--front{left:40px;background:var(--card-dark)}
  .card--back{left:620px;background:var(--card-light)}

  /* front */
  .front-art{position:absolute;inset:0}
  .brand{position:absolute;font-family:"Roboto",sans-serif;font-weight:400;letter-spacing:.14em;text-transform:uppercase;white-space:nowrap}
  .card--front .brand{left:262px;top:34px;font-size:19px;color:var(--white)}
  .name{position:absolute;left:262px;top:82px;font-size:38px;font-weight:900;color:var(--red);line-height:1}
  .name-tab{position:absolute;right:0;top:82px;width:14px;height:38px;background:var(--red)}
  .title{position:absolute;left:264px;top:126px;font-size:15px;color:var(--white)}
  .company{position:absolute;left:264px;top:160px;font-size:15px;color:var(--white)}
  .contacts{position:absolute;left:264px;top:202px;list-style:none}
  .contacts li{display:flex;align-items:center;gap:10px;font-size:14px;color:var(--white);height:26px}
  .contacts svg{width:16px;height:16px;flex:none}

  /* back */
  .card--back .brand{left:0;right:0;top:40px;text-align:center;font-size:24px;color:var(--ink)}
  .guarantee{position:absolute;left:0;right:0;top:100px;text-align:center;font-size:17px;font-weight:900;color:var(--red);letter-spacing:.01em}
  .divider{position:absolute;left:34px;right:34px;top:136px;display:flex;align-items:center;gap:10px}
  .divider::before,.divider::after{content:"";flex:1;height:2px;background:var(--blue)}
  .divider span{font-size:16px;font-weight:900;color:var(--blue);white-space:nowrap}
  .services{position:absolute;left:24px;right:24px;top:166px;text-align:center;line-height:28px;font-size:13.5px;color:var(--ink)}
  .service{display:inline-flex;align-items:center;gap:4px;margin:0 5px;white-space:nowrap}
  .service svg{width:11px;height:11px}
</style>
</head>
<body>
<main class="stage">

  <section class="card card--front" aria-label="Business card front">
    <svg class="front-art" viewBox="0 0 540 310" width="540" height="310">
      <defs>
        <linearGradient id="roomTone" x1="0" y1="0" x2="1" y2="1">
          <stop offset="0" stop-color="var(--photo-b)"/>
          <stop offset=".55" stop-color="var(--photo-a)"/>
          <stop offset="1" stop-color="#c4c8cc"/>
        </linearGradient>
      </defs>
      <path d="M0 0 H205 C250 90 240 220 170 310 H0 Z" fill="var(--red)"/>
      <path d="M0 0 H192 C236 90 226 220 156 310 H0 Z" fill="url(#roomTone)" role="img" aria-label="Photo of a bright remodelled living room with large windows and a white sofa"/>
    </svg>
    <div class="brand">Harborline Builders</div>
    <div class="name">Marcus Delling</div>
    <div class="name-tab"></div>
    <div class="title">Licensed General Contractors</div>
    <div class="company">Harborline Builders Inc.</div>
    <ul class="contacts">
      <li><svg viewBox="0 0 24 24"><path fill="var(--red)" d="M6.6 10.8a15 15 0 0 0 6.6 6.6l2.2-2.2c.3-.3.7-.4 1-.2 1.1.4 2.3.6 3.6.6.6 0 1 .4 1 1V20c0 .6-.4 1-1 1C10.6 21 3 13.4 3 4c0-.6.4-1 1-1h3.5c.6 0 1 .4 1 1 0 1.3.2 2.5.6 3.6.1.3 0 .7-.2 1z"/></svg>858-471-6093</li>
      <li><svg viewBox="0 0 24 24"><rect x="2" y="5" width="20" height="14" rx="2" fill="var(--red)"/><path d="M3 7l9 6 9-6" fill="none" stroke="var(--card-dark)" stroke-width="1.8"/></svg>info@brightoakbuilders.com</li>
      <li><svg viewBox="0 0 24 24"><circle cx="12" cy="12" r="10" fill="var(--red)"/><path d="M2 12h20M12 2c3 3 3 17 0 20M12 2c-3 3-3 17 0 20" fill="none" stroke="var(--card-dark)" stroke-width="1.5"/></svg>www.brightoakbuilders.com</li>
    </ul>
  </section>

  <section class="card card--back" aria-label="Business card back">
    <div class="brand">Harborline Builders</div>
    <div class="guarantee">OUR SERVICES ARE 100% GUARANTEED</div>
    <div class="divider"><span>SPECIALIZING IN:</span></div>
    <p class="services">
      <span class="service"><svg viewBox="0 0 12 12"><circle cx="6" cy="6" r="5" fill="none" stroke="var(--red)" stroke-width="1.3"/><path d="M3.5 6l2 2 3-4" fill="none" stroke="var(--red)" stroke-width="1.5"/></svg>Remodel: Kitchen &amp; Bath</span>
      <span class="service"><svg viewBox="0 0 12 12"><circle cx="6" cy="6" r="5" fill="none" stroke="var(--red)" stroke-width="1.3"/><path d="M3.5 6l2 2 3-4" fill="none" stroke="var(--red)" stroke-width="1.5"/></svg>Painting: Interior &amp; Exterior</span>
      <span class="service"><svg viewBox="0 0 12 12"><circle cx="6" cy="6" r="5" fill="none" stroke="var(--red)" stroke-width="1.3"/><path d="M3.5 6l2 2 3-4" fill="none" stroke="var(--red)" stroke-width="1.5"/></svg>Flooring: Carpet, Vinyl, Wood</span>
      <span class="service"><svg viewBox="0 0 12 12"><circle cx="6" cy="6" r="5" fill="none" stroke="var(--red)" stroke-width="1.3"/><path d="M3.5 6l2 2 3-4" fill="none" stroke="var(--red)" stroke-width="1.5"/></svg>Window &amp; Door Replacement</span>
      <span class="service"><svg viewBox="0 0 12 12"><circle cx="6" cy="6" r="5" fill="none" stroke="var(--red)" stroke-width="1.3"/><path d="M3.5 6l2 2 3-4" fill="none" stroke="var(--red)" stroke-width="1.5"/></svg>Plumbing: Repairs &amp; Upgrades</span>
      <span class="service"><svg viewBox="0 0 12 12"><circle cx="6" cy="6" r="5" fill="none" stroke="var(--red)" stroke-width="1.3"/><path d="M3.5 6l2 2 3-4" fill="none" stroke="var(--red)" stroke-width="1.5"/></svg>Energy-Efficient Upgrades</span>
      <span class="service"><svg viewBox="0 0 12 12"><circle cx="6" cy="6" r="5" fill="none" stroke="var(--red)" stroke-width="1.3"/><path d="M3.5 6l2 2 3-4" fill="none" stroke="var(--red)" stroke-width="1.5"/></svg>Deck &amp; Patio Construction</span>
      <span class="service"><svg viewBox="0 0 12 12"><circle cx="6" cy="6" r="5" fill="none" stroke="var(--red)" stroke-width="1.3"/><path d="M3.5 6l2 2 3-4" fill="none" stroke="var(--red)" stroke-width="1.5"/></svg>Water &amp; Mold Damage</span>
      <span class="service"><svg viewBox="0 0 12 12"><circle cx="6" cy="6" r="5" fill="none" stroke="var(--red)" stroke-width="1.3"/><path d="M3.5 6l2 2 3-4" fill="none" stroke="var(--red)" stroke-width="1.5"/></svg>Garage Renovation</span>
    </p>
  </section>

</main>
</body>
</html>
```